Modern Medical Optometry Website

We need mordern, Patient friendly website. Easy to navigate and enhance our advance medical technology and excellent patient care.
1. HOME PAGE
2. OUR TEAM PAGE
3. EYECARE PAGE - VISION SERVICES, EYE EXAMS, KERATOCONUS CENTER, GLAUCOMA , DIABITES, MELORIDEX EXAM, DIGITAL RETINAL, OCT.
4. MYOPIA CONTROL CLINIC
5. DRY EYE CLINIC
6. EYEWEAR
7. PATIENT CENTER - BLOG
7. CONTACT US
This is our current website www.brivaloka.com
and We want to add more content and a cleaner design like these website
http://tarnwickfolvendale.com/
https://www.qmvorlu.com/

```html
<!DOCTYPE html>
<html lang="en">
<head>
<meta charset="utf-8">
<title>Contact Lenses – Lumivo Optometry</title>
<link rel="stylesheet" href="https://fonts.googleapis.com/css2?family=Montserrat:wght@400;600;700&family=Open+Sans:wght@400;600;700&display=swap">
<style>
:root{
  --teal:#1fa3b8;
  --teal-dark:#178a9c;
  --yellow:#f3c814;
  --ink:#333a3f;
  --muted:#8a9196;
  --band:#eef1f2;
  --pill:#3a3a3a;
  --white:#ffffff;
}
*{box-sizing:border-box;margin:0;padding:0}
html,body{width:829px;height:1200px;overflow:hidden;background:var(--white)}
body{font-family:"Open Sans",Arial,sans-serif;color:var(--ink);position:relative}
.topbar{height:26px;background:var(--teal);display:flex;align-items:center;justify-content:flex-end;padding:0 40px;gap:18px;font-size:9px;color:var(--white)}
.topbar .item{display:flex;align-items:center;gap:5px}
.topbar .dots{display:flex;gap:7px}
.topbar .dot{width:9px;height:9px;border-radius:50%;background:rgba(255,255,255,.85)}
.header{height:66px;display:flex;align-items:center;justify-content:space-between;padding:0 40px;border-bottom:1px solid #e6e9ea}
.brand{display:flex;align-items:center;gap:8px;font-family:"Montserrat",sans-serif;font-weight:700;font-size:13px;color:var(--teal);letter-spacing:.5px}
.brand .mark{width:34px;height:34px;background:var(--yellow)}
.nav{display:flex;gap:16px;font-family:"Montserrat",sans-serif;font-size:9.5px;font-weight:600;color:#5b6368;letter-spacing:.3px}
.nav a{color:inherit;text-decoration:none;padding:6px 0}
.nav a.active{color:var(--teal);border-bottom:2px solid var(--teal)}
.page-title{height:98px;background:var(--band);display:flex;align-items:center;justify-content:center;font-family:"Montserrat",sans-serif;font-weight:700;font-size:27px;color:var(--teal);letter-spacing:.5px}
.intro{display:flex;gap:45px;padding:34px 40px 0}
.intro .photo{width:290px;height:195px;flex:none;background:radial-gradient(circle at 55% 50%,#8fb9c4 0,#c9d9dc 35%,#e9dcd3 70%,#d8c2b4 100%)}
.intro .text{flex:1}
.intro h2{font-family:"Montserrat",sans-serif;font-size:14.5px;font-weight:700;color:var(--teal);line-height:1.4;margin-bottom:10px}
.intro .lead{font-size:9.5px;font-weight:700;color:var(--ink);line-height:1.55;margin-bottom:9px}
.intro p{font-size:9px;color:var(--muted);line-height:1.6;margin-bottom:8px}
.types{padding:38px 40px 0}
.types h2{font-family:"Montserrat",sans-serif;font-size:20px;font-weight:700;color:var(--teal);padding-bottom:8px;position:relative}
.types h2::after{content:"";position:absolute;left:0;bottom:0;width:38px;height:2px;background:var(--teal)}
.cols{display:flex;gap:50px;margin-top:22px}
.col{flex:1}
.col h3{font-family:"Montserrat",sans-serif;font-size:12.5px;font-weight:700;color:var(--ink);line-height:1.4;margin-bottom:10px;min-height:36px}
.col p{font-size:9px;color:var(--muted);line-height:1.6;margin-bottom:18px}
.btn{display:inline-block;padding:10px 22px;font-family:"Montserrat",sans-serif;font-size:9.5px;font-weight:600;color:var(--white);letter-spacing:.4px}
.btn.yellow{background:var(--yellow);color:var(--ink)}
.btn.teal{background:var(--teal)}
.footer{position:absolute;left:0;top:720px;width:829px;height:442px;background:var(--yellow);padding:52px 40px 0;display:flex;gap:40px}
.fcol{flex:1}
.fcol h4{font-family:"Montserrat",sans-serif;font-size:14px;font-weight:700;color:var(--ink);margin-bottom:20px}
.fline{display:flex;align-items:flex-start;gap:10px;font-size:9.5px;color:var(--ink);line-height:1.5;margin-bottom:12px}
.fline svg{flex:none;margin-top:1px}
.directions{display:inline-block;margin-top:10px;background:var(--pill);color:var(--white);font-size:9px;padding:8px 18px;border-radius:14px}
.hours{font-size:9.5px;line-height:1.9;color:var(--ink)}
.hours b{font-weight:700}
.social{display:flex;gap:8px;margin-top:18px}
.social span{width:24px;height:24px;border-radius:50%;background:var(--teal)}
.copyright{position:absolute;left:0;bottom:0;width:829px;height:38px;background:var(--teal);color:var(--white);font-size:9px;display:flex;align-items:center;justify-content:center}
.copyright b{margin:0 4px;font-weight:700}
</style>
</head>
<body>
<div class="topbar">
  <span class="item">
    <svg width="9" height="9" viewBox="0 0 24 24"><path d="M6.6 10.8a15 15 0 006.6 6.6l2.2-2.2a1 1 0 011-.25 11.4 11.4 0 003.6.6 1 1 0 011 1V20a1 1 0 01-1 1A17 17 0 013 4a1 1 0 011-1h3.5a1 1 0 011 1 11.4 11.4 0 00.6 3.6 1 1 0 01-.25 1z" fill="#fff"/></svg>
    555-014-0132
  </span>
  <span class="item">
    <svg width="10" height="8" viewBox="0 0 24 18"><rect x="1" y="1" width="22" height="16" fill="none" stroke="#fff" stroke-width="2"/><path d="M1 1l11 9 11-9" fill="none" stroke="#fff" stroke-width="2"/></svg>
    info@lumivooptometry.com
  </span>
  <span class="dots"><span class="dot"></span><span class="dot"></span><span class="dot"></span><span class="dot"></span></span>
</div>

<header class="header">
  <div class="brand"><span class="mark"></span>LUMIVO OPTOMETRY</div>
  <nav class="nav">
    <a href="#">HOME</a>
    <a href="#">OUR TEAM</a>
    <a href="#" class="active">EYE CARE</a>
    <a href="#">MYOPIA CONTROL CLINIC</a>
    <a href="#">EYEWEAR</a>
    <a href="#">BLOG</a>
    <a href="#">CONTACT US</a>
  </nav>
</header>

<div class="page-title">CONTACT LENSES</div>

<section class="intro">
  <div class="photo" role="img" aria-label="Close-up photo of an eye with a contact lens on a fingertip"></div>
  <div class="text">
    <h2>LOREM IPSUM IS SIMPLY DUMMY TEXT AND PRINTIGN TYPESETTING.</h2>
    <p class="lead">Scleral contacts are large-diameter gas permeable contact lenses specially designed to vault over the entire corneal surface and rest on the "white" of the eye (sclera).</p>
    <p>In doing so, scleral lenses functionally replace the irregular cornea with a perfectly smooth optical surface to correct vision problems caused by keratoconus and other corneal irregularities.</p>
    <p>Also, the space between the cornea and the back surface of a scleral lens acts as a fluid reservoir to provide comfort for people with severe dry eyes who otherwise could not tolerate contact lens wear.</p>
  </div>
</section>

<section class="types">
  <h2>TYPES OF SCLERAL</h2>
  <div class="cols">
    <div class="col">
      <h3>SCLERAL FOR KERATOCONUS</h3>
      <p>Dr. Lumen has recommended scleral contact lenses for a variety of hard-to-fit eyes, including eyes with keratoconus. In cases of early keratoconus, a standard GP lens may be ideal.</p>
      <span class="btn yellow">LEARN MORE</span>
    </div>
    <div class="col">
      <h3>SCLERAL CONTACT LENSES FOR DRY EYES AND OTHER EYE PROBLEMS</h3>
      <p>In addition to keratoconus, scleral contact lenses can be used for eyes that have undergone a corneal transplant, and for people with severe dry eyes caused by conditions such as Sjogren's...</p>
      <span class="btn teal">LEARN MORE</span>
    </div>
  </div>
</section>

<footer class="footer">
  <div class="fcol">
    <h4>Lumivo Optometry</h4>
    <div class="fline"><svg width="11" height="11" viewBox="0 0 24 24"><path d="M6.6 10.8a15 15 0 006.6 6.6l2.2-2.2a1 1 0 011-.25 11.4 11.4 0 003.6.6 1 1 0 011 1V20a1 1 0 01-1 1A17 17 0 013 4a1 1 0 011-1h3.5a1 1 0 011 1 11.4 11.4 0 00.6 3.6 1 1 0 01-.25 1z" fill="#1fa3b8"/></svg>555-014-0132</div>
    <div class="fline"><svg width="11" height="11" viewBox="0 0 24 24"><rect x="5" y="2" width="14" height="7" fill="#1fa3b8"/><rect x="2" y="9" width="20" height="9" fill="#1fa3b8"/><rect x="6" y="15" width="12" height="7" fill="#fff" stroke="#1fa3b8" stroke-width="2"/></svg>555-014-0177</div>
    <div class="fline"><svg width="11" height="9" viewBox="0 0 24 18"><rect x="1" y="1" width="22" height="16" fill="#1fa3b8"/><path d="M1 1l11 9 11-9" fill="none" stroke="#fff" stroke-width="2"/></svg>info@lumivooptometry.com</div>
    <div class="fline"><svg width="10" height="13" viewBox="0 0 20 26"><path d="M10 0a9 9 0 019 9c0 7-9 17-9 17S1 16 1 9a9 9 0 019-9z" fill="#1fa3b8"/><circle cx="10" cy="9" r="3.5" fill="#f3c814"/></svg>7207 Larkspur Row, Brookfield,<br>CA 91873</div>
    <span class="directions">Get directions on the map</span>
  </div>
  <div class="fcol">
    <h4>Cedar Hollow</h4>
    <div class="fline"><svg width="11" height="11" viewBox="0 0 24 24"><path d="M6.6 10.8a15 15 0 006.6 6.6l2.2-2.2a1 1 0 011-.25 11.4 11.4 0 003.6.6 1 1 0 011 1V20a1 1 0 01-1 1A17 17 0 013 4a1 1 0 011-1h3.5a1 1 0 011 1 11.4 11.4 0 00.6 3.6 1 1 0 01-.25 1z" fill="#1fa3b8"/></svg>555-019-2046</div>
    <div class="fline"><svg width="11" height="9" viewBox="0 0 24 18"><rect x="1" y="1" width="22" height="16" fill="#1fa3b8"/><path d="M1 1l11 9 11-9" fill="none" stroke="#fff" stroke-width="2"/></svg>cedarhollow@lumivooptometry.com</div>
    <div class="fline"><svg width="10" height="13" viewBox="0 0 20 26"><path d="M10 0a9 9 0 019 9c0 7-9 17-9 17S1 16 1 9a9 9 0 019-9z" fill="#1fa3b8"/><circle cx="10" cy="9" r="3.5" fill="#f3c814"/></svg>5538 Orrin Vale Blvd, Suite A<br>Cedar Hollow, CA 91346</div>
    <span class="directions">Get directions on the map</span>
  </div>
  <div class="fcol">
    <h4>Opening Hours</h4>
    <div class="hours">
      Monday - Thursday : <b>8 am - 6 pm</b><br>
      Friday : <b>8:30 am - 5 pm</b><br>
      Saturday : <b>8:30 am - 5 pm</b><br>
      Closed on <b>Sundays</b><br>
      Please keep in mind we are closed<br>for <b>lunch 1-2 pm</b>
    </div>
    <div class="social"><span></span><span></span><span></span><span></span></div>
  </div>
</footer>

<div class="copyright">Copyright © <b>LUMIVO OPTOMETRY</b> · 2016 · All rights reserved</div>
</body>
</html>
```